3 Film Posters for a Dark Comedy Feature

We would need 3 distinctive film posters for our movie, Dust over Harbor. It is a comedy-drama about the influence of money. See below the trailer for the movie:
https://www.clipvault-stream.net/watch?v=pq_7TnRwLzB

I have attached a lot of images from the movie. You can use any of the below images in whichever combination you want. I want 3 different posters in which you use between 1 to maximum 5 of the attached images. I'd like at least one image of the 20 euro banknote to be used once or twice in the 3 posters.

Here is the writing that needs to be put on the poster:
Big Title: Dust over Harbor
"A film by Raphael Dumarest"
Actors: Sam Whitley, Nora Fitzsimmons, Declan Hartigan, Peter Ashdown, Tod Lyle

Target Market(s)

Film Festivals, Film Distributors, Chatterbook & Picturegram

Industry/Entity Type

Cinema

Requirements
Must have
• At once in the 3 posters I'd like to see an image of the 20 euro banknote.

```html
<!DOCTYPE html>
<html lang="en">
<head>
<meta charset="utf-8">
<title>Dust over Harbor — Poster</title>
<link rel="stylesheet" href="https://fonts.googleapis.com/css2?family=Montserrat:wght@500;700&family=Sacramento&display=swap">
<style>
  :root {
    --sky-top: #6f7d86;
    --sky-low: #56646d;
    --sea-high: #2f4a63;
    --sea-deep: #233a53;
    --rock: #3b3731;
    --rock-dark: #1f1d1a;
    --glow: rgba(220, 232, 245, 0.75);
    --beam: rgba(190, 210, 228, 0.10);
    --jacket-red: #6e2f2f;
    --jacket-dark: #2a2424;
    --trousers: #5f5d5c;
    --stone: #6a625a;
    --title-gold: #f3b83c;
    --title-shadow: rgba(10, 14, 20, 0.85);
    --rule: #d9dcdf;
    --text-light: #ffffff;
  }
  * { margin: 0; padding: 0; box-sizing: border-box; }
  html, body { width: 848px; height: 1200px; overflow: hidden; background: var(--rock-dark); }
  .poster {
    position: relative;
    width: 848px;
    height: 1200px;
    overflow: hidden;
    font-family: "Montserrat", sans-serif;
    color: var(--text-light);
  }
  .scene-photo {
    position: absolute;
    inset: 0;
    background:
      radial-gradient(ellipse 420px 330px at 410px 0px, var(--glow), rgba(200,215,230,0.25) 45%, transparent 75%),
      linear-gradient(180deg,
        var(--sky-top) 0px,
        var(--sky-low) 222px,
        var(--sea-high) 224px,
        var(--sea-deep) 700px,
        #2a3d4f 940px,
        var(--rock) 1000px,
        #2b2824 1100px,
        var(--rock-dark) 1200px);
  }
  .light-beams {
    position: absolute;
    left: 0;
    top: 0;
    width: 848px;
    height: 700px;
  }
  .figure-photo {
    position: absolute;
    left: 290px;
    top: 650px;
    width: 212px;
    height: 350px;
    border-radius: 90px 90px 30px 30px;
    background:
      linear-gradient(180deg,
        rgba(110, 70, 50, 0.9) 0%,
        var(--jacket-red) 22%,
        var(--jacket-dark) 52%,
        var(--trousers) 70%,
        var(--stone) 88%,
        rgba(59, 55, 49, 0.9) 100%);
    opacity: 0.92;
  }
  .director-credit {
    position: absolute;
    top: 86px;
    left: 0;
    width: 848px;
    text-align: center;
    font-size: 19px;
    font-weight: 500;
    letter-spacing: 0.6em;
    padding-left: 0.6em;
    text-transform: uppercase;
  }
  .header-rule {
    position: absolute;
    top: 135px;
    left: 103px;
    width: 642px;
    height: 3px;
    background: var(--rule);
  }
  .film-title {
    position: absolute;
    top: 160px;
    left: 0;
    width: 848px;
    text-align: center;
    font-family: "Sacramento", cursive;
    font-weight: 400;
    color: var(--title-gold);
    line-height: 1;
    text-shadow: 4px 5px 4px var(--title-shadow);
  }
  .film-title .line { display: block; font-size: 190px; }
  .film-title .line-one { padding-left: 50px; }
  .film-title .line-two { padding-left: 10px; margin-top: -10px; }
  .starring-label {
    position: absolute;
    top: 986px;
    left: 0;
    width: 848px;
    text-align: center;
    font-size: 37px;
    font-weight: 700;
  }
  .cast-list {
    position: absolute;
    top: 1071px;
    left: 0;
    width: 848px;
    height: 60px;
    list-style: none;
  }
  .cast-member {
    position: absolute;
    top: 0;
    width: 180px;
    margin-left: -90px;
    text-align: center;
    font-size: 24px;
    font-weight: 700;
    line-height: 1.2;
    text-transform: uppercase;
  }
</style>
</head>
<body>
  <main class="poster">
    <div class="scene-photo" role="img" aria-label="Film still: calm grey-blue sea under a pale sky, rocky shoreline in the foreground"></div>

    <svg class="light-beams" viewBox="0 0 848 700" aria-hidden="true">
      <g fill="var(--beam)">
        <polygon points="405,0 415,0 150,700 90,700"/>
        <polygon points="405,0 415,0 300,700 250,700"/>
        <polygon points="405,0 415,0 520,700 470,700"/>
        <polygon points="405,0 415,0 690,700 630,700"/>
        <polygon points="405,0 415,0 800,560 760,580"/>
      </g>
    </svg>

    <div class="figure-photo" role="img" aria-label="Photo: a young man with long hair in a red and black jacket sits hunched on a rock at the water's edge"></div>

    <p class="director-credit">A film by Raphael Dumarest</p>
    <div class="header-rule"></div>

    <h1 class="film-title">
      <span class="line line-one">Dust over</span>
      <span class="line line-two">Harbor</span>
    </h1>

    <p class="starring-label">STARRING</p>
    <ul class="cast-list">
      <li class="cast-member" style="left:105px">Sam<br>Whitley</li>
      <li class="cast-member" style="left:274px">Declan<br>Hartigan</li>
      <li class="cast-member" style="left:433px">Peter<br>Ashdown</li>
      <li class="cast-member" style="left:605px">Nora<br>Fitzsimmons</li>
      <li class="cast-member" style="left:764px">Tod<br>Lyle</li>
    </ul>
  </main>
</body>
</html>
```